website design for M&T Electric

A portfolio website for a high end commercial and residential electrical contracting company. The current site mandtelectric.example does not represent the current direction but the images in the gallery give you an idea of the work we do. Current logo will be uploaded shortly but is black text on white background.
Target Market(s)
General Contractors, Residential Home Owners, clients intersted in Velmora home automation.
Industry/Entity Type
Electrician
Coding
Coded - Design and coding required
Number of Pages Required
2 page
Font styles to use
Sans Serif
Colors
Designer to choose colors to be used in the design.
Requirements
Must have
- Portfolio section highlighting different service areas and products (Velmora Housepilot, etc)

```html
<!DOCTYPE html>
<html lang="en">
<head>
<meta charset="utf-8">
<title>M&amp;T Electric</title>
<link href="https://fonts.googleapis.com/css2?family=Roboto+Condensed:wght@400;700&family=Open+Sans:ital,wght@0,400;0,600;1,400&display=swap" rel="stylesheet">
<style>
:root{
  --gold:#d1a526;
  --gold-dark:#b88f1c;
  --ink:#1a1a1a;
  --text:#444;
  --white:#fff;
  --black:#0d0d0d;
  --line:#d9d9d9;
}
*{box-sizing:border-box;margin:0;padding:0}
html,body{width:1200px;height:2866px;overflow:hidden;background:var(--white)}
body{font-family:"Open Sans",Arial,sans-serif;color:var(--text);position:relative}
.cond{font-family:"Roboto Condensed","Arial Narrow",sans-serif}

/* hero */
.hero{position:relative;height:596px;background:linear-gradient(180deg,#1b2430 0%,#2c3a2a 40%,#3f6b2a 75%,#2a4a1e 100%);overflow:hidden}
.hero-photo{position:absolute;inset:0}
.topbar{position:absolute;top:22px;right:86px;display:flex;gap:34px;color:var(--white);font-size:16px}
.topbar span{display:flex;align-items:center;gap:8px}
.brand{position:absolute;left:86px;top:46px;color:#f2f2f2;font-family:"Roboto Condensed",sans-serif;font-size:40px;font-weight:400;letter-spacing:1px}
.nav{position:absolute;top:64px;right:86px;display:flex;align-items:center;gap:30px;font-size:14px;color:var(--white)}
.nav .active{color:var(--gold)}
.nav .quote{background:var(--gold);color:var(--ink);padding:12px 18px;font-weight:600}
.arrow{position:absolute;top:350px;width:26px;height:26px;border-radius:50%;background:var(--white);display:flex;align-items:center;justify-content:center}
.arrow.left{left:26px}.arrow.right{right:22px}
.diamond{position:absolute;left:741px;top:185px;width:364px;height:364px}
.diamond-text{position:absolute;left:741px;top:310px;width:364px;text-align:center;color:var(--ink)}
.diamond-text h2{font-family:"Roboto Condensed",sans-serif;font-size:42px;font-weight:700;line-height:1}
.diamond-text p{font-family:"Roboto Condensed",sans-serif;font-size:18px;margin-top:4px}
.diamond-text .more{font-size:13px;margin-top:16px;display:inline-block}

/* section heading */
.heading{text-align:center;font-family:"Roboto Condensed",sans-serif;font-weight:700;font-size:26px;color:var(--ink)}
.heading::after{content:"";display:block;width:46px;height:3px;background:var(--gold);margin:16px auto 0}

/* services */
.services{padding-top:64px;height:1338px - 596px}
.grid-top{position:absolute;top:747px;left:86px;display:grid;grid-template-columns:336px 336px 336px;gap:10px}
.grid-bottom{position:absolute;top:1005px;left:86px;display:grid;grid-template-columns:250px 250px 250px 248px;gap:10px}
.tile{position:relative;overflow:hidden}
.grid-top .tile{height:249px}
.grid-bottom .tile{height:241px}
.tile .photo{position:absolute;inset:0}
.tile .label{position:absolute;left:0;right:0;bottom:0;height:54px;background:var(--black);color:var(--white);display:flex;align-items:center;justify-content:space-between;padding:0 28px}
.tile .label b{font-family:"Roboto Condensed",sans-serif;font-size:22px;font-weight:700;letter-spacing:.3px}
.tile .label small{font-size:12px}
.tile.featured .label{background:var(--gold);color:var(--ink)}
.grid-bottom .label{justify-content:center;height:50px}
.grid-bottom .label b{font-size:19px}

/* welcome */
.welcome{position:absolute;top:1338px;left:0;width:1200px;height:401px;background:linear-gradient(135deg,#dcb330,#c99e1f 60%,#d8ae2b);text-align:center;color:var(--ink)}
.welcome h2{font-family:"Roboto Condensed",sans-serif;font-size:26px;font-weight:700;margin-top:68px}
.welcome p{width:800px;margin:24px auto 0;font-size:17.5px;line-height:1.62;color:#2a2a2a}
.btn-outline{display:inline-block;margin-top:30px;border:2px solid var(--ink);padding:10px 16px;font-size:14px;border-radius:2px}

/* testimonials */
.testimonials{position:absolute;top:1812px;left:0;width:1200px}
.quote-box{position:absolute;top:80px;left:201px;width:827px;height:220px;border:1.5px solid #e1cf93;text-align:center}
.quote-box p{width:700px;margin:72px auto 0;font-style:italic;font-size:14px;line-height:1.6;color:#555}
.quote-box h4{margin-top:18px;font-size:17px;font-weight:400;color:var(--ink)}
.quote-box .pager{margin-top:14px;font-size:14px;color:var(--ink);letter-spacing:8px}
.quote-mark{position:absolute;top:46px;left:172px;width:68px;height:68px;border-radius:50%;background:var(--gold);display:flex;align-items:center;justify-content:center}
.partners{position:absolute;top:2171px;left:86px;display:grid;grid-template-columns:repeat(6,161px);gap:12.4px}
.partner{height:84px;border:1.5px solid #cfcfcf;display:flex;align-items:center;justify-content:center}
.partner i{display:block;width:70px;height:22px;background:#bdbdbd;border-radius:3px}

/* perks bar */
.perks{position:absolute;top:2318px;left:0;width:1200px;height:94px;background:var(--gold);display:grid;grid-template-columns:1fr 1fr 1fr;align-items:center;color:var(--ink);font-family:"Roboto Condensed",sans-serif;font-size:24px}
.perks div{display:flex;align-items:center;justify-content:center;gap:8px;height:64px}
.perks div+div{border-left:2px solid rgba(255,255,255,.45)}

/* footer */
.footer{position:absolute;top:2412px;left:0;width:1200px;height:454px;background:var(--black);color:#e6e6e6}
.col{position:absolute;top:68px}
.col h5{font-family:"Roboto Condensed",sans-serif;font-size:17px;font-weight:400;color:var(--white);padding-bottom:10px;border-bottom:1px solid #555;width:230px}
.contact{left:88px}
.contact ul{list-style:none;margin-top:20px;font-size:13.5px;line-height:1.5}
.contact li{display:flex;gap:22px;margin-bottom:16px}
.contact li svg{flex:none;margin-top:4px}
.social{display:flex;gap:14px;margin-top:20px}
.social i{display:block;width:22px;height:22px;border-radius:50%;background:#6d6d6d}
.message{left:489px}
.field{width:237px;height:36px;border:1px solid #777;margin-top:14px;padding:8px 12px;font-size:12.5px;color:#8a8a8a}
.field:first-of-type{margin-top:18px}
.field.area{height:62px}
.send{display:inline-block;margin-top:16px;background:var(--gold);color:var(--ink);font-size:13px;font-weight:600;padding:7px 32px}
.newsletter{left:848px}
.newsletter p{font-size:12.5px;line-height:1.6;margin-top:16px;width:270px}
.subscribe{display:flex;margin-top:28px;width:266px;height:48px}
.subscribe span{flex:1;background:var(--white);color:#888;font-size:13px;padding:15px 18px}
.subscribe b{width:56px;background:var(--gold);display:flex;align-items:center;justify-content:center}
.legal{position:absolute;top:359px;left:0;width:1200px;border-top:1px solid #2a2a2a;display:flex;justify-content:space-between;align-items:center;padding:0 88px;height:95px;font-size:12.5px}
.legal nav{display:flex;gap:16px}
.legal nav span.sep{color:#888}
.legal small{font-size:11px;color:#ccc}
</style>
</head>
<body>

<header class="hero">
  <div class="hero-photo" role="img" aria-label="Modern home at dusk with lit windows, green lawn and paved walkway"></div>
  <div class="topbar">
    <span><svg width="16" height="16" viewBox="0 0 24 24"><path fill="#d1a526" d="M6.6 10.8a15 15 0 0 0 6.6 6.6l2.2-2.2c.3-.3.7-.4 1-.2 1.1.4 2.3.6 3.6.6.6 0 1 .4 1 1V20c0 .6-.4 1-1 1A17 17 0 0 1 3 4c0-.6.4-1 1-1h3.5c.6 0 1 .4 1 1 0 1.3.2 2.5.6 3.6.1.3 0 .7-.2 1z"/></svg>: (555) 014-2290</span>
    <span><svg width="17" height="14" viewBox="0 0 24 18"><path fill="#d1a526" d="M0 0h24v3L12 10 0 3zM0 5l12 7 12-7v13H0z"/></svg>: dwarren@mandtelectric.example</span>
  </div>
  <div class="brand">M&amp;T Electric</div>
  <nav class="nav">
    <span class="active">Home</span><span>Gallery</span><span>Specialty Services</span><span>About</span><span>Contact</span>
    <span class="quote">Get A Free Quote</span>
  </nav>
  <span class="arrow left"><svg width="12" height="12" viewBox="0 0 12 12"><path d="M8 1 3 6l5 5" stroke="#111" stroke-width="2.5" fill="none"/></svg></span>
  <span class="arrow right"><svg width="12" height="12" viewBox="0 0 12 12"><path d="M4 1l5 5-5 5" stroke="#111" stroke-width="2.5" fill="none"/></svg></span>
  <svg class="diamond" viewBox="0 0 364 364"><polygon points="182,6 358,182 182,358 6,182" fill="#fff" fill-opacity=".9" stroke="#d1a526" stroke-width="9"/></svg>
  <div class="diamond-text">
    <h2>RESIDENTIAL</h2>
    <p>ELECTRICAL CONTRACTING</p>
    <span class="more">Learn More &#10148;</span>
  </div>
</header>

<section class="services">
  <h2 class="heading" style="position:absolute;top:660px;left:0;width:1200px">SPECIALTY SERVICES</h2>
  <div class="grid-top">
    <div class="tile"><div class="photo" role="img" aria-label="Large stone commercial building under blue sky" style="background:linear-gradient(180deg,#5f8fd0,#8a8178 60%,#4b4238)"></div><div class="label"><b>COMMERCIAL</b><small>Learn More &#10148;</small></div></div>
    <div class="tile featured"><div class="photo" role="img" aria-label="Warm wood-paneled home library with lit shelves" style="background:linear-gradient(180deg,#4a2c18,#8a5a30 50%,#3a2212)"></div><div class="label"><b>RESIDENTIAL</b><small>Learn More &#10148;</small></div></div>
    <div class="tile"><div class="photo" role="img" aria-label="Home exterior with landscape lighting at night" style="background:linear-gradient(180deg,#0d1a3a,#2b3552 50%,#4a3522)"></div><div class="label"><b>LANDSCAPE</b><small>Learn More &#10148;</small></div></div>
  </div>
  <div class="grid-bottom">
    <div class="tile"><div class="photo" role="img" aria-label="Wall-mounted lighting control keypad" style="background:linear-gradient(180deg,#a18a6c,#5b4a3a)"></div><div class="label"><b>VELMORA HOUSEPILOT</b></div></div>
    <div class="tile"><div class="photo" role="img" aria-label="Living room with motorized window shades" style="background:linear-gradient(180deg,#c9c9c6,#8d8a84)"></div><div class="label"><b>VELMORA SHADES</b></div></div>
    <div class="tile"><div class="photo" role="img" aria-label="Three energy efficient light bulbs" style="background:linear-gradient(180deg,#e8e8e8,#cfcfcf)"></div><div class="label"><b>LED LIGHTING</b></div></div>
    <div class="tile"><div class="photo" role="img" aria-label="Standby home generator unit" style="background:linear-gradient(180deg,#f2f2f2,#c7c9cb)"></div><div class="label"><b>EMERGENCY GENERATORS</b></div></div>
  </div>
</section>

<section class="welcome" role="img" aria-label="Gold-tinted backdrop of electrician tools and multimeter">
  <h2>WELCOME TO M &amp; T ELECTRIC</h2>
  <p>M &amp; T Electric is a full service electrical contracting shop. We offer commercial, residential, light industrial, and agricultural services. We're Velmora Housepilot and Velmora Motorized Shades certified, as well as an authorized Brightvolt generator dealer. We've served the Cedar Basin and South Central Idaho area for over 18 years.</p>
  <span class="btn-outline">Learn More &#10148;</span>
</section>

<section class="testimonials">
  <h2 class="heading">TESTIMONIALS</h2>
  <div class="quote-box">
    <p>I love my new heaters. I should have done this years ago. The installation was done professionally and in the time frame allotted. It was a great experience.</p>
    <h4>Daniel R Hayes</h4>
    <div class="pager">&lsaquo; &rsaquo;</div>
  </div>
  <div class="quote-mark"><svg width="32" height="26" viewBox="0 0 32 26"><path fill="#fff" d="M0 26V14C0 6 4 1 12 0v5c-4 1-6 4-6 8h6v13zM18 26V14c0-8 4-13 12-14v5c-4 1-6 4-6 8h6v13z"/></svg></div>
</section>

<div class="partners">
  <div class="partner"><i></i></div><div class="partner"><i></i></div><div class="partner"><i></i></div>
  <div class="partner"><i></i></div><div class="partner"><i></i></div><div class="partner"><i></i></div>
</div>

<section class="perks">
  <div><svg width="20" height="20" viewBox="0 0 20 20"><circle cx="10" cy="10" r="8" fill="none" stroke="#1a1a1a" stroke-width="2.5"/><path d="M10 5v5l3 2" stroke="#1a1a1a" stroke-width="2" fill="none"/></svg>24/HOUR EMERGENCY SERVICE</div>
  <div><svg width="20" height="20" viewBox="0 0 20 20"><circle cx="10" cy="6" r="4.5" fill="#1a1a1a"/><path d="M2 20c0-6 3.5-8 8-8s8 2 8 8z" fill="#1a1a1a"/></svg>FREE CONSULTATIONS</div>
  <div><svg width="20" height="20" viewBox="0 0 24 24"><path fill="#1a1a1a" d="M6.6 10.8a15 15 0 0 0 6.6 6.6l2.2-2.2c.3-.3.7-.4 1-.2 1.1.4 2.3.6 3.6.6.6 0 1 .4 1 1V20c0 .6-.4 1-1 1A17 17 0 0 1 3 4c0-.6.4-1 1-1h3.5c.6 0 1 .4 1 1 0 1.3.2 2.5.6 3.6.1.3 0 .7-.2 1z"/></svg>(555) 014-2290</div>
</section>

<footer class="footer">
  <div class="col contact">
    <h5>CONTACT US</h5>
    <ul>
      <li><svg width="10" height="14" viewBox="0 0 10 14"><path fill="#fff" d="M5 0a5 5 0 0 1 5 5c0 4-5 9-5 9S0 9 0 5a5 5 0 0 1 5-5zm0 3a2 2 0 1 0 0 4 2 2 0 0 0 0-4z"/></svg><span>2217 Harbor Lane, PO Box 4821,<br>Millbrook, ID 83000</span></li>
      <li><svg width="12" height="12" viewBox="0 0 24 24"><path fill="#fff" d="M6.6 10.8a15 15 0 0 0 6.6 6.6l2.2-2.2c.3-.3.7-.4 1-.2 1.1.4 2.3.6 3.6.6.6 0 1 .4 1 1V20c0 .6-.4 1-1 1A17 17 0 0 1 3 4c0-.6.4-1 1-1h3.5c.6 0 1 .4 1 1 0 1.3.2 2.5.6 3.6.1.3 0 .7-.2 1z"/></svg><span>(555) 014-2290</span></li>
      <li><svg width="12" height="10" viewBox="0 0 24 18"><path fill="#fff" d="M0 0h24v3L12 10 0 3zM0 5l12 7 12-7v13H0z"/></svg><span>dwarren@mandtelectric.example</span></li>
      <li><svg width="12" height="10" viewBox="0 0 24 18"><path fill="#fff" d="M0 0h24v3L12 10 0 3zM0 5l12 7 12-7v13H0z"/></svg><span>kmarlow@mandtelectric.example</span></li>
    </ul>
    <div class="social"><i></i><i></i><i></i><i></i></div>
  </div>
  <div class="col message">
    <h5>SEND US A MESSAGE</h5>
    <div class="field">Name</div>
    <div class="field">Email</div>
    <div class="field area">Message</div>
    <span class="send">SEND</span>
  </div>
  <div class="col newsletter">
    <h5 style="width:266px">NEWSLETTER SUBSCRIBE</h5>
    <p>Subscribe to our newsletter and we will inform you about newest Projects.</p>
    <div class="subscribe"><span>Your email</span><b><svg width="22" height="20" viewBox="0 0 22 20"><path d="M1 9 21 1l-4 18-6-6-4 5v-7l12-9-14 8z" fill="none" stroke="#1a1a1a" stroke-width="1.6" stroke-linejoin="round"/></svg></b></div>
  </div>
  <div class="legal">
    <nav><span>Home</span><span class="sep">|</span><span>Gallery</span><span class="sep">|</span><span>Specialty Services</span><span class="sep">|</span><span>About</span><span class="sep">|</span><span>Contact</span></nav>
    <small>Copyright &copy; 2017, M &amp; T Electric. All rights reserved.</small>
  </div>
</footer>

</body>
</html>
```